Skincare Clinic specializing in treating difficult skin conditions needs a web design

We want to restructure and rehash our current webdesigns. The current ones are dated and look very old fashioned also, they are not structured well.

The current websites need to get an uplift in look and become more classy and modern with navigation ease by structuring the information into ease of access

The current web address is
www.brightdermhaven.com.au and
www.lumacutis.com.au

We also have international Partner website which is good and we need to better than them. So this website will act as a guide to better the new site
www.dermacalm-drtorvelle.com

But the new site should be more inclined towards a Blue colour or Aqua marine blue orientation and it needs to be Scientific giving authenticity to the medical industry we operate in.

Attached is a webdesign framework and architecture we would want to adopt. It is a schematic diagram and you can creatively adopt based on what you want to propose.

The website needs to be coded and Should be coded in WordPress such that it helps with SEO activity and nexora promoline pickup.

We will need the necessary pictures and we could provide them or agree to by them from the designers source.

Target Market(s)

Patients with Skin Disease and people interested to book consultation or buy products for their Skin condition

Industry/Entity Type

Clinic

Coding

Coded - Design and coding required

Number of Pages Required

5+ page

Font styles to use
Other font styles liked:
• Use a light font denoting class.

Requirements
Must have
• Should be modern, Easy to navigate, mobile friendly and coded in wordpress
• Blue colour and should look scientific and medicinal
Nice to have
• Classy and creative
Should not have
• No Green colour or herbal look

```html
<!DOCTYPE html>
<html lang="en">
<head>
<meta charset="utf-8">
<title>brightdermhaven — Skin Clinic</title>
<link rel="stylesheet" href="https://fonts.googleapis.com/css2?family=Raleway:wght@300;400;500&family=Open+Sans:ital,wght@0,400;0,600;0,700;1,400&display=swap">
<style>
:root{
  --page:#ffffff;
  --ink:#2b2b2b;
  --body:#4a4a4a;
  --blue:#1f8fe0;
  --blue-light:#25aef0;
  --blue-deep:#0d5fcf;
  --teal:#4aa3b5;
  --teal-light:#93cfd6;
  --teal-deep:#64aeb6;
  --line:#a9d8f2;
  --footer-top:#1aa0ee;
  --footer-bottom:#1a86e0;
}
*{box-sizing:border-box;margin:0;padding:0}
html,body{width:1134px;height:1200px;overflow:hidden;background:var(--page)}
body{position:relative;font-family:"Raleway",sans-serif;color:var(--ink)}
.abs{position:absolute}

/* header */
.promo-strip{left:169px;top:20px;width:370px;height:82px;border-radius:3px;
  background:linear-gradient(90deg,#e7e4e2 0%,#eeeeee 50%,#d9dcdf 100%);padding:20px 0 0 26px}
.promo-strip h2{font-weight:500;font-size:20px;color:#1f1f1f;letter-spacing:.1px}
.promo-strip p{font-size:12.5px;color:#2c2c2c;margin-top:5px}
.brand{left:690px;top:36px;display:flex;align-items:center;gap:12px}
.brand-name{font-family:"Raleway",sans-serif;font-weight:500;font-size:31px;color:var(--teal);letter-spacing:-.5px}
.brand-mark{width:52px;height:52px;border-radius:50%;background:var(--blue)}

/* navigation */
.main-nav{left:170px;top:115px;width:793px;height:43px;display:flex;
  background:linear-gradient(180deg,#29a9ee,#1a8ae0)}
.main-nav a{flex:1;display:flex;align-items:center;justify-content:center;color:#fff;
  text-decoration:none;font-size:14px;border-right:1px solid rgba(255,255,255,.45)}
.main-nav a:last-child{border-right:none}

/* hero */
.hero{left:170px;top:158px;width:793px;height:328px;
  background:linear-gradient(100deg,#dfe6ec 0%,#eef1f4 35%,#c9cfd6 62%,#e8d6cc 100%)}
.hero-caption{left:36px;top:89px;width:323px;height:137px;background:rgba(24,118,214,.88);
  padding:22px 0 0 32px;color:#fff}
.hero-caption .kicker{font-size:18px;font-weight:400}
.hero-caption h1{font-size:29px;font-weight:400;line-height:1.1;margin-top:2px}
.hero-caption p{font-family:"Open Sans",sans-serif;font-size:10px;line-height:16px;margin-top:8px;color:#e4f0fb}
.hero-dots{left:367px;top:306px;display:flex;gap:5px}
.hero-dots span{width:15px;height:15px;border-radius:50%;background:#fff}

/* action cards */
.action-card{top:500px;width:254px;height:142px;border-radius:8px;color:#fff;text-align:center;padding-top:18px}
.action-card svg{display:block;margin:0 auto;height:52px}
.action-card h3{font-size:18px;font-weight:500;margin-top:20px;letter-spacing:.3px}
.action-card p{font-size:13px;margin-top:6px;color:#d9efff;letter-spacing:.3px}
.card-consult{left:170px;background:linear-gradient(180deg,#1fb0f0,#1784e4)}
.card-purchase{left:440px;background:linear-gradient(180deg,#1b8fea,#0d5fcf)}
.card-practice{left:709px;background:linear-gradient(180deg,#93cfd6,#64aeb6)}
.card-practice p{color:#e5f5f7}

.section-rule{left:170px;top:670px;width:793px;height:5px;border-top:1px solid var(--line);border-bottom:1px solid var(--line)}

/* content */
.section-title{font-size:22px;font-weight:400;color:#222}
.body-copy{font-family:"Open Sans",sans-serif;font-size:9px;line-height:16.6px;color:var(--body)}
.about{left:173px;top:714px;width:390px}
.about .body-copy{margin-top:10px}
.cases{left:598px;top:713px;width:365px}
.case-arrows{left:342px;top:6px}
.case-strip{left:0;top:37px;display:flex;gap:5px}
.case-thumb{width:88px;height:93px;border:1px solid #d6d6d6;border-radius:2px;overflow:hidden;background:#f3f3f3}
.case-photo{height:68px}
.case-thumb span{display:block;text-align:center;font-size:12px;line-height:24px;color:#222;font-weight:500}
.unique{left:171px;top:890px;width:390px}
.unique h2{font-size:23px;font-weight:300;color:var(--teal);line-height:1.1}
.unique h2 small{display:block;font-size:18px}
.unique-photo{left:0;top:62px;width:112px;height:80px;background:linear-gradient(135deg,#ecdcc6,#c9b7a0 60%,#8e7b6a)}
.unique .body-copy{position:absolute;left:125px;top:58px;width:265px}
.testimonials{left:596px;top:890px;width:370px}
.testimonials h2{font-size:23px;font-weight:400;color:var(--blue)}
.testimonials .sub{font-family:"Open Sans",sans-serif;font-size:13px;color:#222;margin:4px 0 0 3px}
.avatar{left:0;top:60px;width:73px;height:73px;border-radius:50%;border:3px solid #fff;
  box-shadow:0 0 0 1px #ccc;background:radial-gradient(circle at 50% 45%,#e6cdbd,#b7b7b7 70%)}
.quote{left:80px;top:55px;width:275px;font-family:"Open Sans",sans-serif;font-style:italic;font-size:10.5px;line-height:17px;color:#4c4c4c}
.quote-author{left:80px;top:132px;font-family:"Open Sans",sans-serif;font-weight:600;font-size:10.5px;color:var(--blue)}

/* footer */
.site-footer{left:0;top:1094px;width:1134px;height:106px;background:linear-gradient(180deg,var(--footer-top),var(--footer-bottom))}
.footer-nav{left:173px;top:32px;color:#fff;font-size:14px}
.footer-nav a{color:#fff;text-decoration:none}
.footer-nav i{font-style:normal;margin:0 6px}
.copyright{left:173px;top:58px;font-family:"Open Sans",sans-serif;font-size:10.5px;color:#d8ecfb}
.social{left:888px;top:34px;display:flex;gap:4px}
.social span{width:21px;height:21px;border-radius:3px;background:#fff}
</style>
</head>
<body>

<header>
  <div class="abs promo-strip">
    <h2>Mauris vel lacus vitae felis</h2>
    <p>Etiam est nunc venenatis in tristique eu imperdiet</p>
  </div>
  <div class="abs brand">
    <span class="brand-name">brightdermhaven</span>
    <span class="brand-mark"></span>
  </div>
</header>

<nav class="abs main-nav">
  <a href="#">About Us</a><a href="#">Treatments</a><a href="#">Products</a>
  <a href="#">Results</a><a href="#">Media</a><a href="#">Skin Conditions</a>
</nav>

<section class="abs hero" role="img" aria-label="Doctor in a white coat consulting a patient in a bright clinic">
  <div class="abs hero-caption">
    <div class="kicker">Cum sociis natoque penatibus</div>
    <h1>Skin Treatments</h1>
    <p>Aes massa est sed nisl Class aptent taciti sociosqu ad litora torquent per conubia nostra per inceptos</p>
  </div>
  <div class="abs hero-dots"><span></span><span></span><span></span><span></span></div>
</section>

<a class="abs action-card card-consult">
  <svg viewBox="0 0 52 52" fill="none" stroke="#fff" stroke-width="3" stroke-linecap="round">
    <path d="M12 4h-3v14c0 8 6 13 12 13s12-5 12-13V4h-3"/>
    <path d="M21 31v6c0 7 5 11 11 11s9-4 9-10v-6"/>
    <circle cx="41" cy="28" r="5" fill="#fff"/>
  </svg>
  <h3>CONSULTATION</h3>
  <p>BOOK ONLINE</p>
</a>
<a class="abs action-card card-purchase">
  <svg viewBox="0 0 64 52" fill="none" stroke="#fff" stroke-width="3" stroke-linejoin="round">
    <path d="M18 18L30 4M38 4l8 10"/>
    <path d="M4 20h46l-5 26H10z"/>
    <path d="M8 30h40M10 39h36M20 20v26M30 20v26M40 20v26"/>
    <circle cx="52" cy="22" r="9" fill="#1a7fe2"/>
    <path d="M52 16v11M48 23l4 4 4-4"/>
  </svg>
  <h3>PURCHASE</h3>
  <p>PRODUCT ONLINE</p>
</a>
<a class="abs action-card card-practice">
  <svg viewBox="0 0 60 52" fill="#fff">
    <circle cx="14" cy="12" r="7"/><circle cx="46" cy="12" r="7"/><circle cx="30" cy="16" r="9"/>
    <path d="M2 36c0-8 5-13 12-13 4 0 6 1 8 3-4 3-6 8-6 14H2z"/>
    <path d="M58 36c0-8-5-13-12-13-4 0-6 1-8 3 4 3 6 8 6 14h14z"/>
    <path d="M14 48c0-12 7-19 16-19s16 7 16 19z"/>
  </svg>
  <h3>PRACTITIONERS</h3>
  <p>INTRANET ACCESS</p>
</a>

<div class="abs section-rule"></div>

<section class="abs about">
  <h2 class="section-title">About Dr Adrian Velmont</h2>
  <p class="body-copy">In massa libero interdum nec interdum vel blandit sed nulla In ullamcorper est eget tempor cursus neque mi consectetuer mi a ultricies massa est sed nisl Class aptent taciti sociosqu ad litora torquent per conubia nostra per inceptos hymenaeos<br>Donec dictum lectus non odio Cras a ante vitae enim iaculis aliquam Mauris nunc quam venenatis nec euismod sit amet egestas placerat est Pellentesque</p>
</section>

<section class="abs cases">
  <h2 class="section-title">Case Studies</h2>
  <svg class="abs case-arrows" width="24" height="16" viewBox="0 0 24 16" fill="none" stroke="#555" stroke-width="1.5">
    <path d="M8 2L3 8l5 6M16 2l5 6-5 6"/>
  </svg>
  <div class="abs case-strip">
    <div class="case-thumb"><div class="case-photo" role="img" aria-label="Skin condition before treatment" style="background:linear-gradient(160deg,#d9b6a8,#b58676 60%,#3b2a26)"></div><span>Before</span></div>
    <div class="case-thumb"><div class="case-photo" role="img" aria-label="Skin after treatment" style="background:linear-gradient(160deg,#e7c9bd,#c7958a 60%,#2b2220)"></div><span>After</span></div>
    <div class="case-thumb"><div class="case-photo" role="img" aria-label="Skin condition before treatment" style="background:linear-gradient(160deg,#d8b08a,#c79a5c 55%,#8d6a4e)"></div><span>Before</span></div>
    <div class="case-thumb"><div class="case-photo" role="img" aria-label="Skin after treatment" style="background:linear-gradient(160deg,#c9917a,#a26b58 60%,#4a3630)"></div><span>After</span></div>
  </div>
</section>

<section class="abs unique">
  <h2>What’s Unique about our<small>treatment Protocols</small></h2>
  <div class="abs unique-photo" role="img" aria-label="Clinic doctor in a white coat holding a treatment product"></div>
  <p class="body-copy">In massa libero interdum nec interdum vel blandit sed nulla In ullamcorper est eget tempor cursus neque mi consectetuer mi a ultricies massa est sed nisl Class aptent taciti sociosqu ad litora torquent per conubia nostra per inceptos hymenaeos<br>Donec dictum lectus non odio Cras</p>
</section>

<section class="abs testimonials">
  <h2>Testimonials</h2>
  <p class="sub">Patients and Media</p>
  <div class="abs avatar" role="img" aria-label="Portrait of a smiling patient"></div>
  <p class="abs quote">Donec dictum lectus non odio Cras a ante vitae enim iaculis aliquam Mauris nunc quam venenatis nec euismod sit amet egestas placerat est Pellentesque habitant morbi tristique senectus et netus et malesuada fames</p>
  <p class="abs quote-author">By Author Name</p>
</section>

<footer class="abs site-footer">
  <div class="abs footer-nav">
    <a href="#">About Us</a><i>|</i><a href="#">Treatments</a><i>|</i><a href="#">Products</a><i>|</i><a href="#">Results</a><i>|</i><a href="#">Media</a><i>|</i><a href="#">Skin Conditions</a>
  </div>
  <p class="abs copyright">© 2015 Company Name &nbsp;All right reserved &nbsp;Term of Use</p>
  <div class="abs social" aria-label="Social links"><span></span><span></span><span></span></div>
</footer>

</body>
</html>
```